professional business card design for technology company

We are a small technology consulting firm, specialising in consulting based around Cloud and Managed services. Our colour scheme is yellow, blue and white, as you can see in the logos. Although we are based in melbourne australia, due to the nature of our work, our clients can be located anywhere. We are looking for a clean, professional, positive look - similar to our company logo

Target Market(s)

small business

Industry/Entity Type

Business

Contact Information for Business Card

eye catching, designed to incorporate some level of raised printing. Must contain website address, phone number, name and job title

Requirements
Must have
• Logo (attached) - use of the same colour scheme

```html
<!DOCTYPE html>
<html lang="en">
<head>
<meta charset="utf-8">
<title>Nimbral Business Card</title>
<link rel="stylesheet" href="https://fonts.googleapis.com/css2?family=Lato:wght@400;700&family=Raleway:wght@400;500&display=swap">
<style>
  :root {
    --stage: #434242;
    --paper: #f5f9fa;
    --brand-blue: #38a6de;
    --sun-yellow: #fcd405;
    --ink: #111111;
    --white: #ffffff;
  }
  * { margin: 0; padding: 0; box-sizing: border-box; }
  html, body {
    width: 1200px;
    height: 900px;
    overflow: hidden;
    background: var(--stage);
  }
  .canvas {
    position: relative;
    width: 1200px;
    height: 900px;
  }
  .card {
    position: absolute;
  }
  .card-front {
    left: 166px;
    top: 134px;
    width: 376px;
    height: 638px;
    background: var(--paper);
  }
  .card-back {
    left: 667px;
    top: 134px;
    width: 383px;
    height: 644px;
    background: var(--brand-blue);
  }
  .accent-band {
    position: absolute;
    left: 91px;
    width: 178px;
    height: 31px;
    background: var(--brand-blue);
  }
  .accent-band.top { top: 0; }
  .accent-band.bottom { bottom: 0; }

  .brand-mark {
    position: absolute;
    left: 0;
    right: 0;
    top: 140px;
    display: flex;
    justify-content: center;
    align-items: center;
    gap: 12px;
  }
  .brand-dot {
    width: 18px;
    height: 18px;
    border-radius: 50%;
    background: var(--sun-yellow);
  }
  .brand-name {
    font-family: 'Lato', sans-serif;
    font-weight: 700;
    font-size: 40px;
    color: var(--brand-blue);
    line-height: 1;
  }

  .person {
    position: absolute;
    left: 0;
    right: 0;
    top: 258px;
    text-align: center;
  }
  .person-name {
    font-family: 'Raleway', sans-serif;
    font-weight: 400;
    font-size: 34px;
    color: var(--ink);
    letter-spacing: 0.5px;
    line-height: 1;
  }
  .person-title {
    margin-top: 7px;
    font-family: 'Raleway', sans-serif;
    font-weight: 400;
    font-size: 17px;
    color: var(--brand-blue);
  }
  .address {
    position: absolute;
    left: 0;
    right: 0;
    top: 371px;
    text-align: center;
    font-family: 'Lato', sans-serif;
    font-size: 19px;
    line-height: 20px;
    color: var(--ink);
    font-style: normal;
  }
  .contact-list {
    position: absolute;
    left: 84px;
    top: 460px;
    list-style: none;
    font-family: 'Lato', sans-serif;
    font-size: 19px;
    color: var(--ink);
  }
  .contact-item {
    display: flex;
    align-items: center;
    height: 25px;
  }
  .contact-icon {
    width: 14px;
    height: 14px;
    margin-right: 18px;
    fill: var(--brand-blue);
    stroke: var(--brand-blue);
  }

  .back-brand {
    position: absolute;
    left: 55px;
    top: 503px;
    display: flex;
    align-items: center;
    gap: 14px;
  }
  .back-dot {
    width: 22px;
    height: 22px;
    border-radius: 50%;
    background: var(--white);
  }
  .back-name {
    font-family: 'Lato', sans-serif;
    font-weight: 700;
    font-size: 46px;
    color: var(--white);
    line-height: 1;
  }
</style>
</head>
<body>
<main class="canvas">
  <section class="card card-front" aria-label="Business card front">
    <div class="accent-band top"></div>

    <div class="brand-mark">
      <span class="brand-dot"></span>
      <span class="brand-name">Nimbral</span>
    </div>

    <div class="person">
      <h1 class="person-name">JOHN SMITH</h1>
      <p class="person-title">Managing Director</p>
    </div>

    <address class="address">1234, Address Goes Here<br>Country Name, 123456</address>

    <ul class="contact-list">
      <li class="contact-item">
        <svg class="contact-icon" viewBox="0 0 14 14" aria-hidden="true">
          <path stroke="none" d="M2 5c0-2 2-3 5-3s5 1 5 3v1H9.5V4.8h-5V6H2z M4 7h6l2 5H2z"/>
        </svg>
        <span>823-456-7890</span>
      </li>
      <li class="contact-item">
        <svg class="contact-icon" viewBox="0 0 14 14" aria-hidden="true">
          <rect x="1" y="3" width="12" height="8" stroke="none"/>
          <path d="M1.5 3.5 7 8l5.5-4.5" fill="none" stroke="#f5f9fa" stroke-width="1.2"/>
        </svg>
        <span>info@youremail.com</span>
      </li>
      <li class="contact-item">
        <svg class="contact-icon" viewBox="0 0 14 14" aria-hidden="true">
          <g fill="none" stroke-width="1.6">
            <rect x="1.5" y="6" width="6" height="3.5" rx="1.75" transform="rotate(-45 4.5 7.75)"/>
            <rect x="6.5" y="4.5" width="6" height="3.5" rx="1.75" transform="rotate(-45 9.5 6.25)"/>
          </g>
        </svg>
        <span>www.yourweb.com</span>
      </li>
    </ul>

    <div class="accent-band bottom"></div>
  </section>

  <section class="card card-back" aria-label="Business card back">
    <div class="back-brand">
      <span class="back-dot"></span>
      <span class="back-name">Nimbral</span>
    </div>
  </section>
</main>
</body>
</html>
```